goal design

We are rolling out a goal for the next 3 years. the goal is as follows:
2014: $8 million gross profit, $1.25 million net income
2015: $12 million gross profit, $2.4 million net income
2016 $15 million gross profit, $4 million net income
We want a design that captures these numbers and that we can publish company wide that will quickly remind everyone of these goals. Our website is www.brackenfieldcrew.com. This will be an internal campaign. We will use the simple design to remind our people of our goals for the next 3 years. We will print it on mouse pads, shirts and things of this nature periodically to keep it front of mind for our people. So easy to remember, visually appealing and simple are good guidelines.
Updates
Target Market(s)
This is an internal campaign. it is to remind our people of our goals for the next few years so will be on little reminder items (i.e. cell phone covers, mouse pads, shirts, screen savers, etc).
Industry/Entity Type
It Company
Look and feel

```html
<!DOCTYPE html>
<html lang="en">
<head>
<meta charset="utf-8">
<title>Brackenfield Crew – Three-Year Goals</title>
<link rel="stylesheet" href="https://fonts.googleapis.com/css2?family=Oswald:wght@700&family=Roboto+Condensed:wght@700&display=swap">
<style>
  :root {
    --paper: #ffffff;
    --ink: #111111;
    --goal-2014: #ec1c7c;
    --goal-2015: #27a9e1;
    --goal-2016: #f7941d;
    --bar-text: #ffffff;
  }
  html, body {
    margin: 0;
    padding: 0;
    overflow: hidden;
    background: var(--paper);
  }
  .canvas {
    position: relative;
    width: 1200px;
    height: 999px;
    background: var(--paper);
    overflow: hidden;
  }
  .brand-name {
    position: absolute;
    left: 318px;
    top: 352px;
    height: 294px;
    margin: 0;
    writing-mode: vertical-rl;
    transform: rotate(180deg);
    font-family: "Roboto Condensed", sans-serif;
    font-weight: 700;
    font-size: 38px;
    line-height: 40px;
    letter-spacing: 3px;
    color: var(--ink);
    text-align: center;
    text-transform: uppercase;
  }
  .goal {
    position: absolute;
    z-index: 1;
    left: 415px;
    display: flex;
    flex-direction: column;
    justify-content: center;
    padding-left: 17px;
    box-sizing: border-box;
    font-family: "Roboto Condensed", sans-serif;
    font-weight: 700;
    color: var(--bar-text);
  }
  .goal p { margin: 0; white-space: nowrap; }
  .goal--2014 { top: 355px; width: 308px; height: 93px; background: var(--goal-2014); font-size: 23px; line-height: 31px; }
  .goal--2015 { top: 454px; width: 377px; height: 92px; background: var(--goal-2015); font-size: 28px; line-height: 35px; }
  .goal--2016 { top: 552px; width: 446px; height: 93px; background: var(--goal-2016); font-size: 28px; line-height: 35px; }
  .year {
    position: absolute;
    z-index: 2;
    margin: 0;
    height: 96px;
    writing-mode: vertical-rl;
    font-family: "Oswald", sans-serif;
    font-weight: 700;
    font-size: 54px;
    line-height: 60px;
    letter-spacing: -2px;
    white-space: nowrap;
  }
  .year--2014 { left: 731px; top: 354px; color: var(--goal-2014); }
  .year--2015 { left: 800px; top: 452px; color: var(--goal-2015); }
  .year--2016 { left: 868px; top: 550px; color: var(--goal-2016); }
</style>
</head>
<body>
  <main class="canvas">
    <h1 class="brand-name">Brackenfield<br>Crew</h1>

    <section class="goal goal--2014">
      <p>$8 million gross profit</p>
      <p>$1.25 million net income</p>
    </section>
    <p class="year year--2014">2014</p>

    <section class="goal goal--2015">
      <p>$12 million gross profit</p>
      <p>$2.4 million net income</p>
    </section>
    <p class="year year--2015">2015</p>

    <section class="goal goal--2016">
      <p>$15 million gross profit</p>
      <p>$4 million net income</p>
    </section>
    <p class="year year--2016">2016</p>
  </main>
</body>
</html>
```